Premium Gold Vodka Label Design

English ------------------- We need a label for a Vodka Bottle. Its a sparkling premium vodka with gold inside. The design should look premium. We tried it on our selves but it looks horrible. Therefore we need your help. The current name is lumora K, but we are open for any better suggestion. We attached the selfmade design. The label will be printed on the bottle. We have other design jobs for you (logo, other sorts)! English ------------------------ We need a label for a vodka bottle. This is a premium vodka which is offset with gold. The design should look like this. We have tried so far and failed. That is why we need your support. The name is so far lumora K. If you have better suggestions we would be pleased about other suggestions / ideas. In the appendix the failed design is stored. The label is to be applied by screen printing. In the case of good work follow-up projects are guaranteed (logo, other varieties, etc)!
Updates

Project Deadline Extended
Reason: We need more time for the decision.

Target Market(s)

USA

Colors

Designer to choose colors to be used in the design.

Requirements
Must have
• English ------------------------ The needed text is on our selfmade label that is attached. English ------------------------ The required texts are stored in the attached design.
Nice to have
• English ------------------------ Transparent places are allowed because we want to print the label on the bottom. English ------------------------ As the label is applied by screen printing, transparent areas are also possible.

```html
<!DOCTYPE html>
<html lang="en">
<head>
<meta charset="utf-8">
<title>Lumora Vodka Label</title>
<link rel="stylesheet" href="https://fonts.googleapis.com/css2?family=Oswald:wght@200;300;400;600;700&display=swap">
<style>
  :root {
    --ink: #161616;
    --silver-light: #f4f4f4;
    --silver-mid: #cdcdcd;
    --silver-dark: #9a9a9a;
    --band: #5a5a5a;
    --band-edge: #b4b4b4;
    --ornament: #1c1c1c;
  }
  html, body {
    margin: 0;
    padding: 0;
    width: 1195px;
    height: 1200px;
    overflow: hidden;
  }
  .label {
    position: relative;
    width: 1195px;
    height: 1200px;
    overflow: hidden;
    background: radial-gradient(ellipse at 50% 45%, var(--silver-light) 0%, var(--silver-mid) 55%, var(--silver-dark) 100%);
    font-family: "Oswald", "Arial Narrow", sans-serif;
    color: var(--ink);
  }
  .metal-sheen {
    position: absolute;
    inset: 0;
    background: linear-gradient(135deg, rgba(255,255,255,0.22), rgba(120,120,120,0.14) 50%, rgba(255,255,255,0.18));
  }
  .edge-band {
    position: absolute;
    left: 0;
    width: 100%;
    background: var(--band);
    border-top: 4px solid var(--band-edge);
    border-bottom: 4px solid var(--band-edge);
    box-sizing: border-box;
  }
  .edge-band--top { top: 0; height: 37px; }
  .edge-band--bottom { bottom: 0; height: 42px; }
  .ornament {
    position: absolute;
    left: 259px;
    width: 677px;
    border-radius: 50%;
    background: radial-gradient(ellipse at center, var(--ornament) 0%, var(--ornament) 45%, rgba(28,28,28,0.75) 75%, rgba(28,28,28,0) 100%);
  }
  .ornament--top { top: 92px; height: 82px; }
  .ornament--bottom { top: 656px; height: 104px; }
  .rule {
    position: absolute;
    left: 86px;
    width: 1023px;
    height: 16px;
  }
  .rule--top { top: 176px; }
  .rule--bottom { top: 637px; }
  .line {
    position: absolute;
    left: 0;
    width: 100%;
    text-align: center;
    line-height: 1;
    white-space: nowrap;
  }
  .tagline { top: 220px; font-size: 80px; font-weight: 200; }
  .brand-name { top: 300px; font-size: 200px; font-weight: 600; letter-spacing: 4px; }
  .spirit-type { top: 541px; font-size: 65px; font-weight: 200; letter-spacing: 0.55em; text-indent: 0.55em; }
  .karat { top: 775px; font-size: 56px; font-weight: 600; }
  .process { top: 866px; font-size: 66px; font-weight: 200; }
  .process strong { font-weight: 600; }
  .origin { top: 961px; font-size: 68px; font-weight: 200; }
  .specs {
    position: absolute;
    top: 1078px;
    left: 0;
    width: 100%;
    display: flex;
    justify-content: center;
    align-items: center;
    font-size: 56px;
    font-weight: 400;
    line-height: 1;
  }
  .specs__item { padding: 0 34px; }
  .specs__divider {
    width: 5px;
    height: 66px;
    background: var(--ink);
  }
</style>
</head>
<body>
  <main class="label">
    <div class="metal-sheen"></div>
    <div class="edge-band edge-band--top"></div>

    <div class="ornament ornament--top" role="img" aria-label="Decorative black scroll ornament"></div>
    <svg class="rule rule--top" viewBox="0 0 1023 16" aria-hidden="true">
      <line x1="8" y1="8" x2="1015" y2="8" stroke="#161616" stroke-width="4"/>
      <circle cx="8" cy="8" r="7" fill="#161616"/>
      <circle cx="1015" cy="8" r="7" fill="#161616"/>
    </svg>

    <div class="line tagline">PREMIUM GOLD&nbsp; SPARKLING</div>
    <div class="line brand-name">LUMORA</div>
    <div class="line spirit-type">VODKA</div>

    <svg class="rule rule--bottom" viewBox="0 0 1023 16" aria-hidden="true">
      <line x1="8" y1="8" x2="1015" y2="8" stroke="#161616" stroke-width="4"/>
      <circle cx="8" cy="8" r="7" fill="#161616"/>
      <circle cx="1015" cy="8" r="7" fill="#161616"/>
    </svg>
    <div class="ornament ornament--bottom" role="img" aria-label="Decorative black scroll ornament"></div>

    <div class="line karat">24 KT</div>
    <div class="line process">DISTILLED <strong>8</strong> FILTERED</div>
    <div class="line origin">MADE IN GERMANY</div>

    <div class="specs">
      <span class="specs__item">40% ALC VOL</span>
      <span class="specs__divider"></span>
      <span class="specs__item">200 ML</span>
      <span class="specs__divider"></span>
      <span class="specs__item">80 PROOF</span>
    </div>

    <div class="edge-band edge-band--bottom"></div>
  </main>
</body>
</html>
```